New travel store signage for Marlow Journeys to attract luxury travellers.

Hello,
We are looking to change the signage of our stores. The signage must include the following:
1. Marlow Journeys Logo (attached)
2. The text...The Travel & Cruise Experts
3. Brand Colours ( Fb0196, 412266, d41d84 and ffffff)
Please note the signage design must be central and only cover two thirds of the store front. We have also attached an image of one of our new stores which might be helpful when preparing a mock up.

We are looking for a quick turnaround on this, making a decision within 48 hours.

Target Market(s)

Retail

Industry/Entity Type

Travel Agency

Font styles to use
Other font styles liked:
• Radley

Colors
E54698
E96AAD
F1A4CE
F9D9EA
FCEFF6
6B429C
8869AF
B7A5CE
E3DAEB
F3F0F8

Requirements
Must have
• Hello, We are looking to change the signage of our stores. The signage must include the following: 1. Marlow Journeys Logo (attached) 2. The text...The Travel & Cruise Experts 3. Brand Colours ( Fb0196, 412266, d41d84 and ffffff) Please note the signage design must be central and only cover two thirds of the store front.
Should not have
• different colour or fonts. Gradient design.

```html
<!DOCTYPE html>
<html lang="en">
<head>
<meta charset="utf-8">
<title>Marlow Journeys – Store Fascia Sign</title>
<link href="https://fonts.googleapis.com/css2?family=Radley&display=swap" rel="stylesheet">
<style>
  :root {
    --brand-purple: #412266;
    --brand-purple-light: #4d2a7a;
    --brand-magenta: #d41d84;
    --brand-pink: #fb0196;
    --brand-pink-soft: #e54698;
    --white: #ffffff;
    --backdrop: #e9e9ec;
  }
  html, body {
    margin: 0;
    padding: 0;
    width: 1200px;
    height: 1117px;
    overflow: hidden;
    background: var(--backdrop);
  }
  .canvas {
    position: relative;
    width: 1200px;
    height: 1117px;
  }
  .fascia-sign {
    position: absolute;
    left: 40px;
    top: 458px;
    width: 1120px;
    height: 200px;
    box-shadow: 0 10px 22px rgba(0, 0, 0, 0.22);
  }
  .fascia-sign__art {
    position: absolute;
    inset: 0;
    width: 100%;
    height: 100%;
    display: block;
  }
  .fascia-sign__brand {
    position: absolute;
    left: 0;
    top: 0;
    width: 420px;
    height: 200px;
    display: flex;
    align-items: center;
    justify-content: center;
    font-family: "Radley", serif;
    font-size: 36px;
    color: var(--brand-purple);
    white-space: nowrap;
  }
  .fascia-sign__tagline {
    position: absolute;
    left: 520px;
    top: 0;
    width: 480px;
    height: 190px;
    margin: 0;
    display: flex;
    flex-direction: column;
    align-items: center;
    justify-content: center;
    font-family: "Radley", serif;
    font-weight: 400;
    font-size: 70px;
    line-height: 0.86;
    color: var(--white);
    text-align: center;
    white-space: nowrap;
  }
</style>
</head>
<body>
<main class="canvas">
  <section class="fascia-sign" aria-label="Marlow Journeys store fascia sign">
    <svg class="fascia-sign__art" viewBox="0 0 1850 330" preserveAspectRatio="none" aria-hidden="true">
      <defs>
        <linearGradient id="stripe-fade" x1="0" y1="0" x2="0" y2="1">
          <stop offset="0" stop-color="var(--brand-purple)"/>
          <stop offset="1" stop-color="var(--brand-magenta)"/>
        </linearGradient>
      </defs>
      <rect class="field-white" x="0" y="0" width="1850" height="330" fill="var(--white)"/>
      <polygon class="stripe-outer" points="640,0 690,0 800,330 750,330" fill="url(#stripe-fade)"/>
      <polygon class="stripe-inner" points="700,0 750,0 860,330 810,330" fill="url(#stripe-fade)"/>
      <polygon class="corner-pink" points="760,0 1850,0 1850,330 870,330" fill="var(--brand-pink-soft)"/>
      <polygon class="panel-edge" points="760,0 1850,0 1850,8 1752,282 870,342" fill="var(--white)"/>
      <polygon class="panel-purple" points="760,0 1836,0 1740,268 870,330" fill="var(--brand-purple)"/>
    </svg>
    <div class="fascia-sign__brand">Marlow Journeys</div>
    <h1 class="fascia-sign__tagline">
      <span>The Travel &amp;</span>
      <span>Cruise Experts</span>
    </h1>
  </section>
</main>
</body>
</html>
```